Business Card Design Project : Ridgeline Press

In preparation for market launch, Tamarind's Ridgeline Press require the development of a business card. Ridgeline Press is a Community online publishing web portal. We provide the the city of Whistler located in B.C. (Canada) business directories, News, Classified ads, News, Events and blogs etc.

The main focus of the brand is to help local businesses to corporate with their online advertisement and marketing. Meeting our clients face to face is a must (B2B).

Target Market(s)

The target market is B2B customers. Business Owners to Marketing, advertising Managers

Industry/Entity Type

Business

Requirements
Must have
• - The business card will be two sided.
the BACK side will have our logo which consist of (icon, url,slogan) submited. The logo will be middle and centred.

The FRONT side should have company details:

Company Legal Name: TAMARIND RIDGELINE MEDIA

Owen Farsk
Director of Sales & Marketing

www.tamarindridgeline.biz
owen@tamarindridgeline.biz

Phone: 604 317 8842
#2714 - 582 E. Halvern St.
Vancouver, B.C. V7K2R4 Canada
Nice to have
• - For the "FRONT" side of our business card. You can separate or re-arrange with our logo components (icon, logo,slogan). It does not have to be together.

Also our company legal name is rather long so arrange or organize the name in a way to make it shorter. Your experience and creativity will have to come in play.
Should not have
• should not have other colors beside logo color and black text (2 colors). Also nothing Three dimensional

```html
<!DOCTYPE html>
<html lang="en">
<head>
<meta charset="utf-8">
<title>Ridgeline Press – Business Card</title>
<link rel="stylesheet" href="https://fonts.googleapis.com/css2?family=Open+Sans:wght@400;600;700&family=Arimo:wght@400;700&display=swap">
<style>
  :root {
    --brand-blue: #1b72b5;
    --ink: #1a1a1a;
    --paper: #ffffff;
    --backdrop: #e6e6e6;
    --rule: #9cc3e2;
  }
  * { box-sizing: border-box; margin: 0; padding: 0; }
  html, body { width: 1200px; height: 944px; overflow: hidden; }
  body {
    background: var(--backdrop);
    position: relative;
    font-family: "Arimo", Arial, sans-serif;
    color: var(--ink);
  }
  .card {
    position: absolute;
    width: 700px;
    height: 400px;
    background: var(--paper);
    overflow: hidden;
  }

  /* Back side: centred logo lockup */
  .card-back { left: 130px; top: 50px; }
  .logo-lockup {
    position: absolute;
    inset: 0;
    display: flex;
    flex-direction: column;
    align-items: center;
    justify-content: center;
    font-family: "Open Sans", Arial, sans-serif;
  }
  .brand-name {
    display: flex;
    align-items: center;
    gap: 14px;
    color: var(--brand-blue);
    font-weight: 700;
    font-size: 44px;
    margin-bottom: 22px;
  }
  .brand-dot {
    width: 26px; height: 26px;
    border-radius: 50%;
    background: var(--brand-blue);
  }
  .brand-url {
    font-weight: 700;
    font-size: 40px;
    letter-spacing: -0.5px;
    color: var(--ink);
    line-height: 1;
  }
  .brand-slogan {
    font-weight: 400;
    font-size: 30px;
    color: var(--brand-blue);
    margin-top: 4px;
  }

  /* Front side: contact details */
  .card-front { left: 370px; top: 494px; }
  .side-band {
    position: absolute;
    left: 0; top: 0;
    width: 90px; height: 100%;
    background: var(--brand-blue);
  }
  .band-slogan, .band-name {
    position: absolute;
    left: 50%;
    color: var(--paper);
    font-family: "Open Sans", Arial, sans-serif;
    white-space: nowrap;
    transform-origin: center;
  }
  .band-slogan {
    top: 105px;
    font-size: 15px;
    transform: translate(-50%, -50%) rotate(-90deg);
  }
  .band-name {
    top: 300px;
    font-size: 17px;
    font-weight: 700;
    transform: translate(-50%, -50%) rotate(-90deg);
  }
  .header-rule {
    position: absolute;
    left: 120px; right: 50px; top: 112px;
    height: 2px;
    background: var(--rule);
  }
  .person {
    position: absolute;
    right: 50px; top: 58px;
    text-align: right;
  }
  .person-name {
    font-family: "Open Sans", Arial, sans-serif;
    color: var(--brand-blue);
    font-size: 25px;
    font-weight: 400;
    line-height: 1;
  }
  .person-title {
    font-size: 14px;
    margin-top: 6px;
  }
  .contact-list {
    position: absolute;
    right: 40px; top: 212px;
    list-style: none;
    font-size: 17px;
    line-height: 21px;
  }
  .contact-list li {
    display: flex;
    justify-content: flex-end;
    align-items: center;
    gap: 12px;
  }
  .contact-list .address { margin-bottom: 16px; }
  .contact-list .address span { text-align: right; }
  .contact-list svg { width: 16px; height: 16px; flex: none; }
  .web-domain { color: var(--brand-blue); }
</style>
</head>
<body>

  <section class="card card-back" aria-label="Business card back">
    <div class="logo-lockup">
      <div class="brand-name"><span class="brand-dot"></span>Ridgeline Press</div>
      <div class="brand-url">www.tamarindridgeline.biz</div>
      <div class="brand-slogan">Your information gateway</div>
    </div>
  </section>

  <section class="card card-front" aria-label="Business card front">
    <div class="side-band">
      <span class="band-slogan">Your information gateway</span>
      <span class="band-name">Ridgeline Press</span>
    </div>

    <div class="person">
      <div class="person-name">Owen Farsk</div>
      <div class="person-title">Director of Sales &amp; Marketing</div>
    </div>
    <div class="header-rule"></div>

    <ul class="contact-list">
      <li class="address">
        <span>#2714 - 582 E. Halvern St.<br>Vancouver, B.C.V7K2R4 Canada</span>
        <svg viewBox="0 0 16 16" aria-hidden="true"><path fill="var(--brand-blue)" d="M8 2 1 8h2v6h4v-4h2v4h4V8h2z"/></svg>
      </li>
      <li>
        <span>604 317 8842</span>
        <svg viewBox="0 0 16 16" aria-hidden="true"><circle cx="8" cy="8" r="7.5" fill="var(--brand-blue)"/><path fill="#fff" d="M5 4h2l1 2.5-1.2 1c.6 1.2 1.5 2.1 2.7 2.7l1-1.2L13 10v2c0 .6-.4 1-1 1C7.6 13 4 9.4 4 5c0-.6.4-1 1-1z"/></svg>
      </li>
      <li>
        <span>owen@tamarindridgeline.biz</span>
        <svg viewBox="0 0 16 16" aria-hidden="true"><circle cx="8" cy="8" r="7.5" fill="var(--brand-blue)"/><rect x="4" y="5" width="8" height="6" fill="#fff"/><path d="M4 5l4 3.2L12 5" fill="none" stroke="var(--brand-blue)" stroke-width="1"/></svg>
      </li>
      <li>
        <span>www.<span class="web-domain">tamarindridgeline</span>.biz</span>
        <svg viewBox="0 0 16 16" aria-hidden="true"><circle cx="8" cy="8" r="7.5" fill="var(--brand-blue)"/><g fill="none" stroke="#fff" stroke-width="0.9"><circle cx="8" cy="8" r="4.5"/><ellipse cx="8" cy="8" rx="2" ry="4.5"/><path d="M3.5 8h9"/></g></svg>
      </li>
    </ul>
  </section>

</body>
</html>
```